Gooey Tides

I am creating an online slime shop that will sell handmade custom slimes. I need to be able to have payment/shipping options and the ability to change product photos since the product and product name will change often

Target Market(s)

Slime

Industry/Entity Type

Retail - online sales

Coding

Coded - Design and coding required

Number of Pages Required

2 page

Font styles to use
Sans Serif

Colors
0094D4
00A9DD
6FCCEA
C7EBF8
E9F6FB
E54698
E96AAD
F1A4CE
F9D9EA
FCEFF6
A7469A
B969AE
D3A5CF
EDDBEB
F8F0F9

Requirements
Must have
• My logo, my domain, ability to change photos of products for sale, payment options, shipping options, social media links, contact us,

```html
<!DOCTYPE html>
<html lang="en">
<head>
<meta charset="utf-8">
<title>Gooey Tides – Handmade Custom Slimes</title>
<link rel="stylesheet" href="https://fonts.googleapis.com/css2?family=Fredoka:wght@500;600;700&family=Josefin+Sans:wght@400;600;700&display=swap">
<style>
:root{
  --pink:#E96AAD;
  --pink-deep:#E54698;
  --pink-mid:#F1A4CE;
  --pink-soft:#F9D9EA;
  --pink-pale:#FCEFF6;
  --purple:#A7469A;
  --purple-mid:#B969AE;
  --purple-soft:#D3A5CF;
  --text:#4a3a48;
  --white:#fff;
  --gold:#F5B301;
}
*{box-sizing:border-box;margin:0;padding:0}
html,body{width:1200px;height:3987px;overflow:hidden}
body{position:relative;background:var(--white);font-family:"Josefin Sans",sans-serif;color:var(--text)}
.abs{position:absolute}
.heading{font-family:"Fredoka",sans-serif;font-weight:600;letter-spacing:2px;text-transform:uppercase}
.btn{display:inline-flex;align-items:center;justify-content:center;font-family:"Fredoka",sans-serif;font-weight:600;font-size:15px;letter-spacing:1.5px;text-transform:uppercase;color:var(--white);background:var(--pink);border-radius:8px;box-shadow:0 0 0 3px var(--white),0 0 0 5px var(--pink);height:42px;padding:0 20px}

/* top bar */
.topbar{top:0;left:0;width:1200px;height:34px;background:var(--pink-soft);text-align:center;font-size:15px;line-height:36px;color:#222}

/* nav */
.nav{top:38px;left:0;width:1200px;height:66px;background:var(--pink);border-top:2px dashed rgba(255,255,255,.8);border-bottom:2px dashed rgba(255,255,255,.8)}
.nav-links{position:absolute;left:308px;top:0;height:62px;display:flex;align-items:center;gap:27px;list-style:none}
.nav-links li{font-family:"Fredoka",sans-serif;font-weight:600;font-size:14px;letter-spacing:1px;color:var(--white);text-transform:uppercase}
.nav-links li.active{color:var(--purple)}
.nav-icons{position:absolute;left:1006px;top:21px;display:flex;gap:14px}
.brand-badge{top:8px;left:111px;width:146px;height:146px;border-radius:50%;background:var(--white);box-shadow:0 0 0 4px var(--pink-soft);display:flex;align-items:center;justify-content:center;text-align:center;font-family:"Fredoka",sans-serif;font-weight:600;font-size:20px;line-height:1.1;color:var(--pink-deep);z-index:3}

/* hero */
.hero{top:108px;left:0;width:1200px;height:550px;background:radial-gradient(circle at 55% 40%,#FBE3EF 0%,var(--pink-soft) 40%,var(--pink-mid) 100%)}
.hero-photo{position:absolute;left:526px;top:0;width:674px;height:550px;background:linear-gradient(135deg,#f6c4dd 0%,#8d6bb3 45%,#e6427e 75%,#f5d75a 100%);opacity:.85}
.hero-copy{position:absolute;left:111px;top:168px}
.hero-copy .kicker{font-family:"Fredoka",sans-serif;font-weight:600;font-size:19px;letter-spacing:2px;color:#111}
.hero-copy h1{font-family:"Fredoka",sans-serif;font-weight:700;font-size:56px;letter-spacing:3px;color:var(--purple);margin-top:14px;text-transform:uppercase}
.hero-copy p{font-size:17px;line-height:25px;color:#222;margin-top:8px;width:420px}
.hero-copy .btn{margin-top:24px}

/* section titles */
.section-title{left:0;width:1200px;text-align:center;font-size:34px}
.section-title .a{color:var(--purple-mid)}
.section-title .b{color:var(--pink-deep)}

/* product cards */
.carousel{left:108px;width:980px;display:flex;gap:26px}
.card{width:226px;height:390px;border:3px solid var(--pink);border-radius:6px;background:var(--white);display:flex;flex-direction:column;align-items:center;text-align:center}
.card .thumb{width:200px;height:115px;margin-top:12px;border-radius:4px}
.card .thumb.full{width:220px;height:156px;margin-top:0;border-radius:2px}
.card .actions{display:flex;gap:10px;margin-top:18px}
.card .actions span{width:30px;height:30px;border-radius:50%;background:var(--white);display:flex;align-items:center;justify-content:center}
.card h3{font-family:"Fredoka",sans-serif;font-weight:600;font-size:20px;letter-spacing:1px;color:var(--pink-deep);margin-top:42px;text-transform:uppercase}
.card .thumb.full + h3{margin-top:28px}
.card .desc{font-size:13px;line-height:20px;color:#555;margin-top:6px;width:200px}
.card .price{font-family:"Fredoka",sans-serif;font-weight:600;font-size:21px;letter-spacing:1px;color:var(--pink-deep);margin-top:10px}
.card .rating{font-size:17px;letter-spacing:1px;color:var(--pink-deep);margin-top:4px}
.card .rating .off{color:var(--pink-soft)}
.card .btn{margin-top:18px;height:38px;padding:0 20px;font-size:14px}
.card.active{background:var(--pink);box-shadow:0 6px 12px rgba(0,0,0,.12)}
.card.active h3,.card.active .desc,.card.active .price,.card.active .rating{color:var(--white)}
.card.active h3{margin-top:14px}
.card.active .btn{box-shadow:0 0 0 2px var(--pink),0 0 0 4px var(--white)}
.arrow{width:34px;height:34px;border-radius:50%;display:flex;align-items:center;justify-content:center}
.arrow.prev{background:var(--pink)}
.arrow.next{border:1.5px solid var(--pink);background:var(--white)}

/* about */
.about{top:1382px;left:0;width:1200px;height:630px;background:var(--pink-pale)}
.about-photo{position:absolute;left:113px;top:73px;width:486px;height:486px;border-radius:50%;background:radial-gradient(circle at 60% 40%,#f6a9c8 0%,#8a6b5a 45%,#5b4a40 80%);box-shadow:0 0 0 3px var(--white),0 0 0 5px var(--pink-mid)}
.about-copy{position:absolute;left:664px;top:140px;width:430px}
.about-copy h2{font-size:34px;letter-spacing:3px}
.about-copy p{font-size:16px;line-height:26px;color:#444;margin-top:18px}
.about-copy .btn{margin-top:26px}

/* custom band */
.custom{top:2724px;left:0;width:1200px;height:353px;background:var(--pink-mid)}
.custom-photo{position:absolute;left:551px;top:0;width:649px;height:353px;background:linear-gradient(120deg,#e9e3dc 0%,#d7cfc9 40%,#f0a8bf 70%,#e5e0da 100%)}
.custom-copy{position:absolute;left:111px;top:56px;width:430px;color:var(--white)}
.custom-copy h2{font-size:38px;line-height:46px;letter-spacing:3px}
.custom-copy p{font-size:16px;line-height:26px;margin-top:10px}
.custom-copy .btn{margin-top:22px}

/* testimonials */
.testimonials{top:3300px;left:105px;width:990px;display:flex}
.quote{flex:1;text-align:center;padding:0 20px;border-right:1px solid #ddd}
.quote:last-child{border-right:none}
.quote .stars{color:var(--gold);font-size:22px;letter-spacing:2px}
.quote p{font-size:16px;line-height:26px;color:#444;margin-top:10px}
.quote .name{font-family:"Fredoka",sans-serif;font-weight:600;font-size:17px;letter-spacing:1px;color:#111;margin-top:8px}
.dots{top:3490px;left:0;width:1200px;display:flex;justify-content:center;gap:6px}
.dots span{width:12px;height:12px;border-radius:50%;border:1.5px solid var(--purple-mid)}
.dots span.on{background:var(--purple-mid);box-shadow:inset 0 0 0 2px #fff}

/* footer */
.footer{top:3600px;left:0;width:1200px;height:387px;background:var(--pink);color:var(--white)}
.footer-brand{position:absolute;left:111px;top:96px;width:300px;text-align:center;font-family:"Fredoka",sans-serif;font-weight:600;font-size:46px;letter-spacing:4px}
.social{position:absolute;left:133px;top:278px;display:flex;gap:14px}
.social span{width:36px;height:36px;border-radius:50%;border:1.5px solid rgba(255,255,255,.7)}
.social span.on{background:var(--white)}
.fcol{position:absolute;top:86px}
.fcol h4{font-family:"Fredoka",sans-serif;font-weight:600;font-size:17px;letter-spacing:1.5px}
.fcol ul{list-style:none;margin-top:18px}
.fcol li{font-size:16px;line-height:34px;padding-left:4px}
.contact li{display:flex;align-items:flex-start;gap:12px;line-height:22px;margin-bottom:18px}
.footer-rule{position:absolute;left:111px;top:330px;width:978px;border-top:1px solid rgba(255,255,255,.6)}
.payments{position:absolute;left:111px;top:344px;display:flex;gap:8px}
.payments span{height:26px;padding:0 8px;border-radius:3px;background:var(--white);color:var(--purple);font-size:12px;font-weight:700;line-height:28px}
.copyright{position:absolute;right:112px;top:352px;font-size:14px}
</style>
</head>
<body>

<div class="abs topbar">Lorem ipsum dolor sit amet, consectetur adipiscing</div>

<header class="abs nav">
  <ul class="nav-links">
    <li class="active">Home</li><li>About Us</li><li>Products</li><li>Shop By Category</li><li>Testimonials</li><li>Blog</li>
  </ul>
  <div class="nav-icons">
    <svg width="18" height="18" viewBox="0 0 18 18" aria-label="Search"><circle cx="7.5" cy="7.5" r="5.5" fill="none" stroke="#fff" stroke-width="2.4"/><line x1="11.5" y1="11.5" x2="16" y2="16" stroke="#fff" stroke-width="2.6" stroke-linecap="round"/></svg>
    <svg width="20" height="18" viewBox="0 0 20 18" aria-label="Cart"><path d="M1 2h3l2.5 9h10l2-6H6" fill="#fff" stroke="#fff" stroke-width="1.5" stroke-linejoin="round"/><circle cx="8" cy="15" r="1.8" fill="#fff"/><circle cx="15" cy="15" r="1.8" fill="#fff"/></svg>
    <svg width="16" height="18" viewBox="0 0 16 18" aria-label="Account"><circle cx="8" cy="5" r="4" fill="#fff"/><path d="M1 17c0-5 3-7 7-7s7 2 7 7z" fill="#fff"/></svg>
  </div>
</header>
<div class="abs brand-badge">Gooey<br>Tides</div>

<section class="abs hero">
  <div class="hero-photo" role="img" aria-label="Two smiling children stretching green and yellow slime"></div>
  <div class="hero-copy">
    <div class="kicker">WELCOME &nbsp;TO</div>
    <h1>Gooey Tides</h1>
    <p>Lorem ipsum dolor sit amet, consectetur dipiscing elit, sed do eiusmod vel facilisis.</p>
    <span class="btn">Shop Now</span>
  </div>
</section>

<h2 class="abs heading section-title" style="top:808px"><span class="a">Featured</span> <span class="b">Products</span></h2>
<div class="abs arrow prev" style="left:45px;top:1075px"><svg width="12" height="14" viewBox="0 0 12 14"><path d="M8 2L3 7l5 5" fill="none" stroke="#fff" stroke-width="2.4"/></svg></div>
<div class="abs arrow next" style="left:1113px;top:1075px"><svg width="12" height="14" viewBox="0 0 12 14"><path d="M4 2l5 5-5 5" fill="none" stroke="#E96AAD" stroke-width="2"/></svg></div>
<div class="abs carousel" style="top:902px">
  <div class="card">
    <div class="thumb" role="img" aria-label="Pink and blue slime spilling from clear tubs" style="background:linear-gradient(90deg,#f07fc0,#f9e3f0 50%,#4ab5f0)"></div>
    <h3>Lorem Ipsum</h3>
    <p class="desc">sed do eiusmod cididunt utsa labore et dolore magna.</p>
    <div class="price">$16.99</div>
    <div class="rating">♥♥♥♥<span class="off">♥</span></div>
    <span class="btn">Shop Now</span>
  </div>
  <div class="card active">
    <div class="thumb" role="img" aria-label="Hands stretching bright pink slime" style="background:linear-gradient(180deg,#f3c7b8,#ee3f95 60%,#f5c6b5)"></div>
    <div class="actions"><span><svg width="16" height="14" viewBox="0 0 16 14"><path d="M8 13S1 8.5 1 4.5A3.5 3.5 0 0 1 8 3a3.5 3.5 0 0 1 7 1.5C15 8.5 8 13 8 13z" fill="#E96AAD"/></svg></span><span><svg width="18" height="12" viewBox="0 0 18 12"><path d="M1 6s3-5 8-5 8 5 8 5-3 5-8 5-8-5-8-5z" fill="none" stroke="#E96AAD" stroke-width="1.5"/><circle cx="9" cy="6" r="2.3" fill="#E96AAD"/></svg></span></div>
    <h3>Lorem Ipsum</h3>
    <p class="desc">sed do eiusmod cididunt utsa labore et dolore magna.</p>
    <div class="price">$16.90</div>
    <div class="rating">♥♥♥♥♥</div>
    <span class="btn">Shop Now</span>
  </div>
  <div class="card">
    <div class="thumb" role="img" aria-label="Red slime spilling from a clear tub" style="background:linear-gradient(90deg,#fff,#ef2d5e 40%,#f5f5f7)"></div>
    <h3>Lorem Ipsum</h3>
    <p class="desc">sed do eiusmod cididunt utsa labore et dolore magna.</p>
    <div class="price">$17.99</div>
    <div class="rating">♥♥♥<span class="off">♥♥</span></div>
    <span class="btn">Shop Now</span>
  </div>
  <div class="card">
    <div class="thumb" role="img" aria-label="Green slime spilling from a clear tub" style="background:linear-gradient(90deg,#fff,#6fd444 40%,#f5f5f7)"></div>
    <h3>Lorem Ipsum</h3>
    <p class="desc">sed do eiusmod cididunt utsa labore et dolore magna.</p>
    <div class="price">$16.80</div>
    <div class="rating">♥♥♥♥♥</div>
    <span class="btn">Shop Now</span>
  </div>
</div>

<section class="abs about">
  <div class="about-photo" role="img" aria-label="Girl stretching pink slime between her hands"></div>
  <div class="about-copy">
    <h2 class="heading"><span style="color:var(--pink-deep)">About</span> <span style="color:var(--purple-mid)">Gooey Tides</span></h2>
    <p>Lorem ipsum dolor sit amet, consectetur adipiscing elit, sed do eiusmod tempor incididunt ut labore et dolore magna aliqua. Quis ipsum suspendisse ultrices gravida. Risus commodo viverra maecenas accumsan lacus vel facilisis.Lorem ipsum dolor sit amet, consectetur dipiscing.</p>
    <p style="margin-top:10px">Lorem ipsum dolor sit amet, consectetur adipiscing elit, sed do eiusmod tempor incididunt ut labore et dolore magna aliqua.</p>
    <span class="btn">Read More</span>
  </div>
</section>

<h2 class="abs heading section-title" style="top:2168px"><span class="b">New Arrival</span> <span class="a">Products</span></h2>
<div class="abs arrow prev" style="left:45px;top:2438px"><svg width="12" height="14" viewBox="0 0 12 14"><path d="M8 2L3 7l5 5" fill="none" stroke="#fff" stroke-width="2.4"/></svg></div>
<div class="abs arrow next" style="left:1113px;top:2438px"><svg width="12" height="14" viewBox="0 0 12 14"><path d="M4 2l5 5-5 5" fill="none" stroke="#E96AAD" stroke-width="2"/></svg></div>
<div class="abs carousel" style="top:2245px">
  <div class="card">
    <div class="thumb full" role="img" aria-label="Hands pulling light blue slime" style="background:linear-gradient(180deg,#2a3550,#8fd3ea 55%,#2d3a55)"></div>
    <h3>Lorem Ipsum</h3>
    <p class="desc">sed do eiusmod cididunt utsa labore et dolore magna.</p>
    <div class="price">$16.99</div>
    <div class="rating">♥♥♥♥<span class="off">♥</span></div>
    <span class="btn">Shop Now</span>
  </div>
  <div class="card">
    <div class="thumb full" role="img" aria-label="Hand squeezing green glitter slime" style="background:linear-gradient(180deg,#6fb2b8,#4da62a 50%,#d9b7a4)"></div>
    <h3>Lorem Ipsum</h3>
    <p class="desc">sed do eiusmod cididunt utsa labore et dolore magna.</p>
    <div class="price">$15.99</div>
    <div class="rating">♥♥♥♥<span class="off">♥</span></div>
    <span class="btn">Shop Now</span>
  </div>
  <div class="card active">
    <div class="thumb" role="img" aria-label="Child holding up purple slime" style="background:linear-gradient(180deg,#f2f2f2,#9b5ad0 50%,#e8dfd8)"></div>
    <div class="actions"><span><svg width="16" height="14" viewBox="0 0 16 14"><path d="M8 13S1 8.5 1 4.5A3.5 3.5 0 0 1 8 3a3.5 3.5 0 0 1 7 1.5C15 8.5 8 13 8 13z" fill="#E96AAD"/></svg></span><span><svg width="18" height="12" viewBox="0 0 18 12"><path d="M1 6s3-5 8-5 8 5 8 5-3 5-8 5-8-5-8-5z" fill="none" stroke="#E96AAD" stroke-width="1.5"/><circle cx="9" cy="6" r="2.3" fill="#E96AAD"/></svg></span></div>
    <h3>Lorem Ipsum</h3>
    <p class="desc">sed do eiusmod cididunt utsa labore et dolore magna.</p>
    <div class="price">$18.99</div>
    <div class="rating">♥♥♥♥♥</div>
    <span class="btn">Shop Now</span>
  </div>
  <div class="card">
    <div class="thumb full" role="img" aria-label="Hand squeezing red and blue swirled slime" style="background:linear-gradient(135deg,#f1f1f1,#d9344f 45%,#3f5bc4 65%,#f1f1f1)"></div>
    <h3>Lorem Ipsum</h3>
    <p class="desc">sed do eiusmod cididunt utsa labore et dolore magna.</p>
    <div class="price">$17.99</div>
    <div class="rating">♥♥♥♥<span class="off">♥</span></div>
    <span class="btn">Shop Now</span>
  </div>
</div>

<section class="abs custom">
  <div class="custom-copy">
    <h2 class="heading">We Sell Handmade Custom Slimes</h2>
    <p>Lorem ipsum dolor sit amet, consectetur adipiscing elit, sed do eiusmod tempor incididunt ut labore et dolore magna aliqua. Quis ipsum suspendissefacilisis.</p>
    <span class="btn">Shop Now</span>
  </div>
  <div class="custom-photo" role="img" aria-label="Girl in a striped top stretching dark glitter slime in a bright room"></div>
</section>

<h2 class="abs heading section-title" style="top:3226px"><span class="b">Client</span> <span class="a">Testimonials</span></h2>
<div class="abs testimonials">
  <div class="quote"><div class="stars">★★★★★</div><p>Lorem ipsum dolor sit amet, onsectetur adipiscing elit, sed do eiusmod tempor incididunt ut labore et dolore magna aliqua.</p><div class="name">Mia Lane</div></div>
  <div class="quote"><div class="stars">★★★★★</div><p>Lorem ipsum dolor sit amet, onsectetur adipiscing elit, sed do eiusmod tempor incididunt ut labore et dolore magna aliqua.</p><div class="name">Theo Park</div></div>
  <div class="quote"><div class="stars">★★★★★</div><p>Lorem ipsum dolor sit amet, onsectetur adipiscing elit, sed do eiusmod tempor incididunt ut labore et dolore magna aliqua.</p><div class="name">Ada Quinn</div></div>
</div>
<div class="abs dots"><span></span><span class="on"></span><span></span></div>

<footer class="abs footer">
  <div class="footer-brand">GOOEY<br>TIDES</div>
  <div class="social">
    <span class="on" aria-label="Social link"></span><span aria-label="Social link"></span><span aria-label="Social link"></span><span aria-label="Social link"></span><span aria-label="Social link"></span>
  </div>
  <div class="fcol" style="left:477px">
    <h4>QUICK LINKS</h4>
    <ul><li>Home</li><li>About Us</li><li>Products</li><li>Shop By Category</li><li>Testimonials</li><li>Blog</li></ul>
  </div>
  <div class="fcol" style="left:683px">
    <h4>INFORMATION</h4>
    <ul><li>FAQ</li><li>Shipping Policy</li><li>Returns</li><li>Track package</li><li>Help Center</li><li>Privacy Policy</li></ul>
  </div>
  <div class="fcol contact" style="left:875px">
    <h4>CONTACT US</h4>
    <ul>
      <li><svg width="18" height="18" viewBox="0 0 18 18"><path d="M4 1l3 4-2 2c1 2.5 3.5 5 6 6l2-2 4 3-2 3C8 17 1 10 1 3z" fill="#fff"/></svg>+1(555) 010 2040</li>
      <li><svg width="18" height="14" viewBox="0 0 18 14"><rect x="1" y="1" width="16" height="12" rx="1" fill="none" stroke="#fff" stroke-width="1.6"/><path d="M1 2l8 6 8-6" fill="none" stroke="#fff" stroke-width="1.6"/></svg>info@gooeytides.com</li>
      <li><svg width="16" height="22" viewBox="0 0 16 22"><path d="M8 21S1 12 1 8a7 7 0 0 1 14 0c0 4-7 13-7 13z" fill="#fff"/><circle cx="8" cy="8" r="2.6" fill="#E96AAD"/></svg>Lorem ipsum dolor sit<br>Gooey Tides, USA</li>
    </ul>
  </div>
  <div class="footer-rule"></div>
  <div class="payments"><span>PayStream</span><span>CardOne</span><span>QuickPay</span><span>TrustCard</span></div>
  <div class="copyright">Copyright © 2024 Gooey Tides all rights reserved.</div>
</footer>

</body>
</html>
```